Real Estate agent needs flyer/folder to contain bio and overview of services

I'm including files of the layout of the small folder. The folder is 6 1/2 across and 9 1/2 inches long. It will have a front & back cover and then writing on the 2 inside pages.

I am sending a few files to incorporate into the flyer, 1 new logo to use and 2 files which are coloring ideas.

Colors

Designer to choose colors to be used in the design.

```html
<!DOCTYPE html>
<html lang="en">
<head>
<meta charset="utf-8">
<title>Carla Moretti – Realtor Folder</title>
<link href="https://fonts.googleapis.com/css2?family=Lato:ital,wght@0,300;0,400;0,700;1,300;1,400&display=swap" rel="stylesheet">
<style>
  :root{
    --stage:#c6c6c8;
    --blue:#0a6fb8;
    --blue-bright:#1391d6;
    --blue-deep:#0b3f86;
    --charcoal:#33363b;
    --slate:#5b616a;
    --paper:#ffffff;
    --paper-shade:#e4e4e6;
    --ink:#2a2a2a;
    --on-dark:#f2f4f6;
  }
  *{box-sizing:border-box;margin:0;padding:0}
  html,body{width:1200px;height:1200px;overflow:hidden}
  body{background:var(--stage);font-family:'Lato',sans-serif;color:var(--ink);position:relative}

  .panel{position:absolute;overflow:hidden}
  .panel svg.bg{position:absolute;inset:0;width:100%;height:100%}

  /* covers spread */
  .back-cover{left:435px;top:25px;width:372px;height:550px}
  .front-cover{left:807px;top:25px;width:372px;height:550px}

  .brand{position:absolute;top:50px;right:30px;display:flex;align-items:center;gap:6px;
    color:var(--on-dark);font-size:12px;font-weight:700;letter-spacing:1px}
  .brand-dot{width:12px;height:12px;border-radius:50%;background:var(--on-dark)}

  .back-quote{position:absolute;left:40px;top:300px;width:280px;text-align:center;
    font-style:italic;font-weight:300;font-size:10.5px;line-height:1.3;color:#333}
  .back-contact{position:absolute;left:90px;top:478px;width:200px;text-align:center;font-size:8px;color:#222;line-height:1.35}
  .back-contact .agent-name{font-size:12px;margin-bottom:8px}
  .back-contact svg{width:7px;height:7px;vertical-align:-1px;margin-right:2px;fill:var(--blue-deep)}

  .agent-mark{position:absolute;left:28px;top:420px;display:flex;align-items:center;gap:8px;
    color:var(--blue-deep);font-size:17px;font-weight:400;letter-spacing:1.5px}
  .agent-mark-square{width:14px;height:14px;background:var(--blue-deep)}

  /* inside spread */
  .inside-left{left:7px;top:596px;width:381px;height:547px;background:linear-gradient(90deg,#1d5aa6 0%,#1170bd 45%,#0f78c4 100%)}
  .inside-right{left:388px;top:596px;width:375px;height:547px;background:linear-gradient(90deg,#60666f 0%,#454a52 55%,#2e3238 100%);color:var(--on-dark)}

  .building-photo{position:absolute;left:0;top:0;width:140px;height:547px;
    background:linear-gradient(90deg,#7f86c0 0%,#6e7ab8 55%,rgba(60,110,185,0) 100%)}
  .title-bar{position:absolute;left:160px;top:28px;width:221px;height:24px;
    background:linear-gradient(90deg,#ffffff,#d9d9db)}
  .intro-col{position:absolute;left:165px;top:0;width:205px;color:var(--on-dark)}
  .section-title{text-align:center;font-size:11px;font-weight:400;letter-spacing:.2px;text-transform:uppercase;color:#e9f2fb}
  .portrait{width:88px;height:88px;border-radius:50%;margin:0 auto;
    background:radial-gradient(circle at 50% 40%,#d9c6ad 0%,#a88d6f 45%,#3a3d44 100%);border:2px solid #d8e6f3}
  .body-copy{font-size:5.3px;line-height:1.32;font-weight:400}
  .body-copy p+p{margin-top:5px}
  .rule{height:1px;background:rgba(255,255,255,.35);width:150px;margin:0 auto}

  .block{position:absolute}
  .right-col{position:absolute;left:42px;width:270px}
  .bar-copy{border-left:1.5px solid var(--on-dark);padding-left:8px;font-size:5.3px;line-height:1.3}
  .bar-copy p+p{margin-top:5px}
  .quote-title{font-size:11px;font-style:italic;letter-spacing:.3px;display:flex;align-items:flex-end;gap:5px}
  .quote-title span.mark{font-size:26px;font-weight:700;font-style:normal;line-height:.6}
  .testimonials{border:1px solid var(--on-dark);border-radius:3px;padding:5px 6px;font-size:5.1px;line-height:1.32;font-style:italic}
  .testimonials .by{text-align:right;font-style:normal;margin:2px 0 6px}
  .testimonials .by:last-child{margin-bottom:0}
</style>
</head>
<body>

<!-- BACK COVER -->
<section class="panel back-cover">
  <svg class="bg" viewBox="0 0 372 550" preserveAspectRatio="none">
    <defs>
      <linearGradient id="paperGrad" x1="0" y1="0" x2="1" y2="0">
        <stop offset="0" stop-color="#ffffff"/><stop offset="1" stop-color="#dedee0"/>
      </linearGradient>
      <linearGradient id="bandGrad" x1="0" y1="0" x2="1" y2="1">
        <stop offset="0" stop-color="#1b8fd6"/><stop offset="1" stop-color="#0b58a6"/>
      </linearGradient>
    </defs>
    <rect width="372" height="550" fill="url(#paperGrad)"/>
    <path d="M0 0 H372 V550 H312 C350 440 335 300 250 215 C180 150 100 115 0 80 Z" fill="url(#bandGrad)"/>
    <path d="M0 0 H372 V545 H320 C355 430 340 290 258 205 C190 140 110 105 0 65 Z" fill="#1aa0e2" opacity=".6"/>
    <path d="M105 0 H372 V215 C320 180 280 140 240 100 C200 60 160 30 105 0 Z" fill="var(--charcoal)"/>
    <path d="M0 92 C110 125 200 160 262 228" stroke="#0b4a94" stroke-width="1" fill="none"/>
  </svg>
  <div class="brand"><span class="brand-dot"></span>SKYLINE REALTY</div>
  <p class="back-quote">Along with being your Realtor, I'm a lifelong resource for all things home-related &amp; beyond...if you need a great referral for anything at all, call me! I can't wait to work with you!</p>
  <div class="back-contact">
    <div class="agent-name">Carla Moretti</div>
    <div><svg viewBox="0 0 10 10"><path d="M2 0.5 L4 2.8 L3 4 C3.8 5.6 4.6 6.4 6 7 L7.2 6 L9.5 8 L8 9.6 C4.5 9.2 0.8 5.5 0.4 2 Z"/></svg>555 014 2280</div>
    <div><svg viewBox="0 0 10 10"><path d="M0.5 2 H9.5 V8 H0.5 Z M0.5 2 L5 5.5 L9.5 2" fill="none" stroke="#0b3f86" stroke-width="1"/></svg>carla@carlamhomes.com</div>
    <div><svg viewBox="0 0 10 10"><circle cx="5" cy="5" r="4.5"/></svg>www.carlamhomes.com</div>
  </div>
</section>

<!-- FRONT COVER -->
<section class="panel front-cover">
  <svg class="bg" viewBox="0 0 372 550" preserveAspectRatio="none">
    <defs>
      <linearGradient id="frontPaper" x1="0" y1="0" x2="1" y2="0">
        <stop offset="0" stop-color="#ffffff"/><stop offset="1" stop-color="#e8e8ea"/>
      </linearGradient>
      <linearGradient id="frontBand" x1="0" y1="0" x2="0" y2="1">
        <stop offset="0" stop-color="#1590d6"/><stop offset="1" stop-color="#0c4f9e"/>
      </linearGradient>
      <linearGradient id="homePhoto" x1="0" y1="0" x2="0" y2="1">
        <stop offset="0" stop-color="#4d8fcf"/><stop offset=".45" stop-color="#c9c8c2"/><stop offset=".85" stop-color="#6f8f52"/><stop offset="1" stop-color="#7fa35a"/>
      </linearGradient>
    </defs>
    <rect width="372" height="550" fill="url(#frontPaper)"/>
    <path d="M0 0 H100 C150 90 170 240 230 340 C280 420 340 470 372 480 V550 H330 C300 470 260 420 215 360 C140 260 80 160 0 80 Z" fill="url(#frontBand)"/>
    <path d="M0 95 C80 170 150 270 205 350 C250 410 300 470 330 550" stroke="#0b3f86" stroke-width=".8" fill="none"/>
    <path d="M100 0 H372 V480 C330 465 285 420 240 340 C190 250 165 100 100 0 Z" fill="#0b5fae"/>
    <path role="img" aria-label="Photograph of a large stone two-storey house under a blue sky" d="M95 0 H372 V455 C330 440 290 400 255 330 C215 250 195 110 95 0 Z" fill="url(#homePhoto)"/>
  </svg>
  <div class="agent-mark"><span class="agent-mark-square"></span>CARLA MORETTI</div>
</section>

<!-- INSIDE LEFT -->
<section class="panel inside-left">
  <div class="building-photo" role="img" aria-label="Photograph of a modern apartment building facade with balconies"></div>
  <div class="title-bar"></div>
  <div class="intro-col">
    <h2 class="section-title block" style="top:67px;width:205px">Let Me Introduce Myself</h2>
    <div class="portrait block" role="img" aria-label="Portrait photo of the agent" style="top:95px;left:58px"></div>
    <div class="body-copy block" style="top:207px;width:205px">
      <p>I'm originally from Chicago, but I'm a full-fledged California girl now. I've lived and worked in Orange County since 1996. I always say where we live is the next best thing to living on a tropical island. I've traveled to many and I'm always happy to come back to my Laguna Niguel home. My passion for this area is why I'm in Real Estate. I consider myself incredibly fortunate to sell homes and help people purchase homes in an area that I love with all my heart.</p>
      <p>This passion also carries over in representing my clients with the highest degree of professionalism, enthusiasm and care. My business is built on exceptional customer service and I'm grateful my clients are mostly repeat and referrals.</p>
    </div>
    <div class="rule block" style="top:313px;left:28px"></div>
    <h2 class="section-title block" style="top:327px;width:205px">My Core Tenet</h2>
    <div class="body-copy block" style="top:347px;width:205px">
      <p>It's All About YOU!</p>
      <p>My #1 priority is understanding YOUR needs and YOUR objectives. This understanding, along with working diligently on your behalf, means we accomplish your goal whether you're purchasing your 1st home or selling a home you've loved so you can move on to the next chapter of your life.</p>
    </div>
    <div class="rule block" style="top:412px;left:28px"></div>
    <h2 class="section-title block" style="top:424px;width:205px;line-height:1.3">Real Estate<br>Services &amp; Beyond...</h2>
    <div class="body-copy block" style="top:462px;width:205px">
      <p>Simply put, I help people who are local, relocating and investing, sell and purchase homes in Southern California. For purchases outside of California, I can refer to a network of agents across the country.</p>
      <p>I also provide a team who is dedicated to providing outstanding customer service throughout the transaction. My team includes a network of lenders, title, and escrow officers, in house CPA, stagers, photographers, contractors and more.</p>
    </div>
  </div>
</section>

<!-- INSIDE RIGHT -->
<section class="panel inside-right">
  <div class="right-col" style="top:60px">
    <h2 class="section-title">Selling Your Home</h2>
    <div class="bar-copy" style="margin-top:10px">
      <p>Selling your home is not like any other business transaction. It's also personal. My priority as your Listing Agent is to guide you through what can be a complicated and sometimes emotional process.</p>
      <p>I place great emphasis on marketing your property with professional photographs, along with harnessing the power of the Internet and the virtual world to reach as many buyers as possible. Your property will be marketed to the public as well as to other agents, thus creating maximum exposure of your home.</p>
      <p>When we first meet to discuss selling your home, it's essential for me to gain an understanding of your unique needs such as timelines, expectations and financial considerations, just to name a few. From there, I begin the process of listing and marketing your home. I lead you through negotiations and more paperwork than you ever care to do, guiding you to the successful closing of your home.</p>
    </div>
  </div>
  <div class="right-col" style="top:200px">
    <h2 class="section-title">Buying a Home</h2>
    <div class="bar-copy" style="margin-top:12px">
      <p>If you're thinking about buying a home, it's imperative you have an accomplished, real estate professional by your side to walk you through what is likely the largest purchase of your life.</p>
      <p>To get started, I like to meet with you so we have an opportunity to get to know each other as purchasing a home is a uniquely personal endeavor. At that time, we can discuss your goals and if it's a good time for you to purchase a home.</p>
      <p>From there, the first step is to obtain a pre-approval from a lender. I'm able to recommend various lenders who can introduce and explain the various loan products available.</p>
      <p>After you've been pre-approved, that's when the fun starts. I guide you through the home buying adventure every step of the way and look forward to handing you the keys to your new home.</p>
    </div>
  </div>
  <div class="right-col" style="top:334px">
    <div class="quote-title"><span class="mark">&ldquo;</span>TESTIMONIALS:</div>
  </div>
  <div class="right-col testimonials" style="top:352px;left:47px;width:276px">
    <p>Carla got us an amazing deal on our new home and sold our old home in a week. Carla is patient, hardworking, professional and most importantly HONEST. Carla is definitely one of the best in the business!</p>
    <p class="by">Nadia &amp; Owen Pierce</p>
    <p>Carla is the kind of Real Estate professional everyone wants to represent them. She is knowledgeable, ethical, energetic, and follows up on every detail. Her honesty, integrity and expertise combined make her a very special and remarkable professional. We were lucky to find her!</p>
    <p class="by">Gordon &amp; Ellen Shaw</p>
    <p>During the home buying process, Carla becomes your trusted advisor, mentor and friend. Her knowledge of the industry, community and market are best in class. A true professional! Carla aligned her goals with my own and understood the motivation behind my purchase. Carla is unequivocally the reason why I was able to purchase my home in Laguna Niguel and provide my family with a world-class community. Without her guidance and experience, I would still be in the market attempting to navigate the ever-changing world of real estate.</p>
    <p class="by">Marisol Vega</p>
  </div>
</section>

</body>
</html>
```